Local Roofing/Construction company business needs new biz card design

We need a new business card design, current cards are from the start of this operation and generic at best. We are a local Construction Company (General Contractor) with a majority of our work originating from insurance claims-exterior finish work is the main focus (Roofs-Siding-Gutters etc). Heavily involved with homeowners and the low ball offers they receive from insurance company's after a insurable event takes place. I have attached some of our original logo file(s) below.

```html
<!DOCTYPE html>
<html lang="en">
<head>
<meta charset="utf-8">
<title>Ironvale Construction – Business Card</title>
<link rel="stylesheet" href="https://fonts.googleapis.com/css2?family=Montserrat:wght@400;500;700;800&display=swap">
<style>
  :root {
    --bg-top: #d4d4d4;
    --bg-bottom: #a9a9a9;
    --card: #0f1f22;
    --card-deep: #0b181b;
    --green: #4cbb6a;
    --green-soft: #2f6f45;
    --pattern-a: #15292d;
    --pattern-b: #1c3a40;
    --white: #f2f4f3;
    --muted: #dfe5e3;
  }
  * { box-sizing: border-box; margin: 0; padding: 0; }
  html, body { width: 1200px; height: 802px; overflow: hidden; }
  body {
    background: linear-gradient(180deg, var(--bg-top), var(--bg-bottom));
    font-family: "Montserrat", sans-serif;
    position: relative;
  }
  .card {
    position: absolute;
    top: 241px;
    width: 525px;
    height: 300px;
    border-radius: 22px;
    background: var(--card);
    border-bottom: 4px solid var(--green);
    box-shadow: 0 18px 30px rgba(0,0,0,0.28);
    overflow: hidden;
  }
  .card--front { left: 55px; }
  .card--back { left: 620px; }

  /* Front */
  .brand-block {
    position: absolute;
    left: 40px;
    top: 112px;
    width: 196px;
    height: 58px;
    display: flex;
    align-items: center;
    gap: 10px;
  }
  .brand-mark {
    width: 14px; height: 14px;
    background: var(--green);
    flex: none;
  }
  .brand-name {
    color: var(--green);
    font-weight: 700;
    font-size: 15px;
    line-height: 1.2;
    letter-spacing: 0.5px;
    text-transform: uppercase;
  }
  .divider {
    position: absolute;
    left: 258px;
    top: 60px;
    width: 1px;
    height: 120px;
    background: var(--green-soft);
  }
  .contact {
    position: absolute;
    left: 280px;
    top: 52px;
  }
  .contact__name {
    color: var(--green);
    font-weight: 800;
    font-size: 21px;
    letter-spacing: 0.8px;
    text-transform: uppercase;
  }
  .contact__role {
    color: var(--white);
    font-size: 12.5px;
    margin-top: 2px;
  }
  .contact__list {
    list-style: none;
    margin-top: 18px;
  }
  .contact__item {
    display: flex;
    align-items: center;
    gap: 8px;
    color: var(--white);
    font-size: 12.5px;
    line-height: 22px;
  }
  .contact__item svg { width: 10px; height: 10px; flex: none; }
  .address {
    position: absolute;
    left: 40px;
    bottom: 34px;
    color: var(--white);
    font-size: 13px;
    letter-spacing: 0.3px;
  }

  /* Back */
  .pattern-field {
    position: absolute;
    inset: 0;
    background:
      radial-gradient(ellipse at 85% 15%, var(--pattern-b), transparent 65%),
      linear-gradient(160deg, var(--pattern-a), var(--card-deep));
  }
  .back-brand {
    position: absolute;
    right: 36px;
    bottom: 56px;
    display: flex;
    align-items: center;
    gap: 6px;
  }
  .back-brand .brand-mark { width: 10px; height: 10px; }
  .back-brand .brand-name { font-size: 11px; }
</style>
</head>
<body>
  <section class="card card--front">
    <div class="brand-block">
      <span class="brand-mark"></span>
      <span class="brand-name">Ironvale<br>Construction</span>
    </div>
    <div class="divider"></div>
    <div class="contact">
      <h1 class="contact__name">Marcus Hale</h1>
      <p class="contact__role">Managing Director</p>
      <ul class="contact__list">
        <li class="contact__item">
          <svg viewBox="0 0 10 10"><path d="M2 1 L4 3 L3 4 Q4.5 6 6 7 L7 6 L9 8 L8 9.5 Q3 9 0.5 2 Z" fill="var(--green)"/></svg>
          0400 555 127
        </li>
        <li class="contact__item">
          <svg viewBox="0 0 10 10"><rect x="0.5" y="2" width="9" height="6.5" fill="var(--green)"/><path d="M0.5 2 L5 6 L9.5 2" stroke="var(--card)" fill="none" stroke-width="1"/></svg>
          info@ironvalebuild.com
        </li>
        <li class="contact__item">
          <svg viewBox="0 0 10 10"><circle cx="5" cy="5" r="4.5" fill="var(--green)"/><path d="M0.5 5 H9.5 M5 0.5 Q2 5 5 9.5 M5 0.5 Q8 5 5 9.5" stroke="var(--card)" fill="none" stroke-width="0.8"/></svg>
          www.ironvalebuild.com
        </li>
      </ul>
    </div>
    <p class="address">1450 W Harlow Road Brenton County 5140</p>
  </section>

  <section class="card card--back">
    <div class="pattern-field" role="img" aria-label="Repeating faint brand pattern in dark teal tones"></div>
    <div class="back-brand">
      <span class="brand-mark"></span>
      <span class="brand-name">Ironvale</span>
    </div>
  </section>
</body>
</html>
```